Ridgewaytrek.com is a mountain biking and climbing travel company. We need a advertisement fo...

We need a advertisement for the back cover of a guide book. We would like a simple but strong ad that includes our logo. It must state that we are a biking and climbing company and people can contact us at the web site ridgewaytrek.com We would like you to incorparate and below photo and logo on the ad.

```html
<!DOCTYPE html>
<html lang="en">
<head>
<meta charset="UTF-8">
<title>Ridgeway Trek – Climbing + Riding</title>
<link rel="stylesheet" href="https://fonts.googleapis.com/css2?family=Josefin+Sans:wght@400;600;700&family=Orbitron:wght@700;900&display=swap">
<style>
  :root {
    --brand-blue: #0c5cb6;
    --accent-orange: #f2a21b;
    --pill-gold: #b8822a;
    --paper-light: #f6f6f6;
    --paper-grey: #c4c5c7;
    --ink: #1d1d1d;
    --white: #ffffff;
  }
  * { margin: 0; padding: 0; box-sizing: border-box; }
  html, body { width: 900px; height: 1200px; overflow: hidden; background: #e6e6e6; }
  .ad {
    position: relative;
    width: 900px; height: 1200px;
    background: radial-gradient(ellipse at 50% 72%, var(--paper-light) 0%, #e3e4e5 50%, var(--paper-grey) 100%);
    font-family: "Josefin Sans", sans-serif;
    color: var(--ink);
    overflow: hidden;
  }
  .header-band {
    position: absolute; left: 0; top: 0; width: 900px; height: 209px;
    background: var(--brand-blue);
    display: flex; align-items: center; justify-content: center;
  }
  .brand-mark { display: flex; align-items: center; gap: 24px; }
  .brand-dot { width: 80px; height: 80px; border-radius: 50%; background: var(--white); }
  .brand-name {
    font-weight: 700; font-size: 84px; letter-spacing: 3px;
    color: var(--white); line-height: 1; padding-top: 12px;
  }
  .hero { position: absolute; left: 0; top: 209px; width: 900px; height: 540px; }
  .hero-title {
    position: absolute; left: 0; top: 437px; width: 900px; text-align: center;
    font-family: "Orbitron", sans-serif; font-weight: 900; font-size: 64px;
    color: var(--white); letter-spacing: 3px; line-height: 72px;
    text-shadow: 0 2px 6px rgba(0,0,0,.6);
  }
  .hero-tagline {
    position: absolute; left: 0; top: 543px; width: 900px; text-align: center;
    font-size: 31px; font-weight: 400; color: var(--accent-orange); letter-spacing: 0.5px;
    text-shadow: 0 1px 3px rgba(0,0,0,.35);
  }
  .activity { position: absolute; top: 760px; width: 230px; height: 230px; }
  .activity svg { width: 230px; height: 230px; display: block; }
  .activity--ride { left: 57px; }
  .activity--climb { left: 335px; }
  .activity--coast { left: 613px; }
  .web-pill {
    position: absolute; left: 194px; top: 1016px; width: 512px; height: 42px;
    border-radius: 21px; background: var(--pill-gold);
    color: var(--white); font-size: 28px; font-weight: 600; text-align: center; line-height: 47px;
  }
  .contact-phone {
    position: absolute; left: 0; top: 1077px; width: 900px; text-align: center;
    font-size: 20px; font-weight: 600;
  }
  .contact-address {
    position: absolute; left: 0; top: 1113px; width: 900px; text-align: center;
    font-size: 19px; line-height: 26px;
  }
  .footer-band { position: absolute; left: 0; bottom: 0; width: 900px; height: 20px; background: var(--brand-blue); }
</style>
</head>
<body>
<main class="ad">
  <header class="header-band">
    <div class="brand-mark">
      <span class="brand-dot"></span>
      <span class="brand-name">RIDGEWAY</span>
    </div>
  </header>

  <svg class="hero" viewBox="0 0 900 540" aria-hidden="true">
    <defs>
      <linearGradient id="street-tones" x1="0" y1="0" x2="0" y2="1">
        <stop offset="0" stop-color="#4b3a2b"/>
        <stop offset="0.18" stop-color="#a4794a"/>
        <stop offset="0.35" stop-color="#8a6a55"/>
        <stop offset="0.55" stop-color="#5d5b5e"/>
        <stop offset="0.78" stop-color="#7c7a7a"/>
        <stop offset="1" stop-color="#96938f"/>
      </linearGradient>
    </defs>
    <path d="M0 0 H900 V492 Q450 598 0 431 Z" fill="url(#street-tones)" role="img" aria-label="Photo of a rider in motion blur on a cobbled old-town street at dusk, lit shopfronts on both sides"/>
    <path d="M0 452 Q450 585 900 474" fill="none" stroke="var(--accent-orange)" stroke-width="4"/>
    <path d="M0 431 Q450 598 900 492" fill="none" stroke="var(--brand-blue)" stroke-width="5"/>
  </svg>

  <h1 class="hero-title">RIDGEWAY TREK</h1>
  <p class="hero-tagline">CLIMBING + RIDING</p>

  <section class="activity-row">
    <div class="activity activity--ride">
      <svg viewBox="0 0 230 230">
        <defs>
          <linearGradient id="ridge-tones" x1="0" y1="0" x2="0" y2="1">
            <stop offset="0" stop-color="#1f6fd0"/>
            <stop offset="0.4" stop-color="#6fa6e0"/>
            <stop offset="0.5" stop-color="#6f7a6a"/>
            <stop offset="0.62" stop-color="#9a8a4e"/>
            <stop offset="1" stop-color="#7a6c3a"/>
          </linearGradient>
        </defs>
        <circle cx="115" cy="115" r="112" fill="#f4f4f4" stroke="#222" stroke-width="2"/>
        <path d="M16 90 A102 102 0 0 1 120 13" fill="none" stroke="var(--brand-blue)" stroke-width="5"/>
        <path d="M208 150 A102 102 0 0 1 100 216" fill="none" stroke="var(--brand-blue)" stroke-width="5"/>
        <path d="M195 52 A102 102 0 0 1 217 120" fill="none" stroke="var(--accent-orange)" stroke-width="3"/>
        <circle cx="115" cy="115" r="97" fill="url(#ridge-tones)" role="img" aria-label="Photo of mountain bikers on a grassy alpine ridge under blue sky"/>
      </svg>
    </div>
    <div class="activity activity--climb">
      <svg viewBox="0 0 230 230">
        <defs>
          <linearGradient id="rock-tones" x1="0" y1="0" x2="1" y2="0">
            <stop offset="0" stop-color="#8a7868"/>
            <stop offset="0.35" stop-color="#a48a72"/>
            <stop offset="0.6" stop-color="#6a5a4c"/>
            <stop offset="0.8" stop-color="#4f6a3c"/>
            <stop offset="1" stop-color="#3e5a2e"/>
          </linearGradient>
        </defs>
        <circle cx="115" cy="115" r="112" fill="#f4f4f4" stroke="#222" stroke-width="2"/>
        <path d="M30 62 A102 102 0 0 1 175 30" fill="none" stroke="var(--accent-orange)" stroke-width="3"/>
        <path d="M214 130 A102 102 0 0 1 60 203" fill="none" stroke="#111" stroke-width="6"/>
        <circle cx="115" cy="115" r="97" fill="url(#rock-tones)" role="img" aria-label="Photo of a climber on a tall rock face surrounded by trees"/>
      </svg>
    </div>
    <div class="activity activity--coast">
      <svg viewBox="0 0 230 230">
        <defs>
          <linearGradient id="coast-tones" x1="0" y1="0" x2="0" y2="1">
            <stop offset="0" stop-color="#4d86c8"/>
            <stop offset="0.3" stop-color="#a9c4df"/>
            <stop offset="0.45" stop-color="#c8c4b8"/>
            <stop offset="0.6" stop-color="#3f78a8"/>
            <stop offset="0.75" stop-color="#a8a8a6"/>
            <stop offset="1" stop-color="#8e8c88"/>
          </linearGradient>
        </defs>
        <circle cx="115" cy="115" r="112" fill="#f4f4f4" stroke="#222" stroke-width="2"/>
        <path d="M13 120 A102 102 0 0 1 110 13" fill="none" stroke="var(--brand-blue)" stroke-width="5"/>
        <path d="M217 115 A102 102 0 0 1 115 217" fill="none" stroke="var(--accent-orange)" stroke-width="3"/>
        <circle cx="115" cy="115" r="97" fill="url(#coast-tones)" role="img" aria-label="Photo of a pebble beach below white coastal cliffs and the sea"/>
      </svg>
    </div>
  </section>

  <div class="web-pill">www.ridgewaytrek.com</div>
  <p class="contact-phone">+41 79 555 0142</p>
  <p class="contact-address">Chemin des Vergers 12, Aubonne, Switzerland<br>14 Banksia Road, Scarborough, Perth, Western Australia</p>

  <div class="footer-band"></div>
</main>
</body>
</html>
```